Valdane Companies Business Card Design

We need a new business card for our Private Equity Real Estate Development firm, “Valdane” and our EB-5 regional center “Thornmere Regional Center” on one card. We prefer a design that is simple, elegant, and represents the luxury products we design and build as well as the financial security and stability our successful history has produced. We are an industry leader in our field and 3rd generation family business that has evolved into an institutional quality investment platform. Considered design size is standard business card dimensions (3.5 x 2 inches with an additional 1/8 inch space for design elements or backgrounds that extend beyond the finished size of your piece.

Target Market(s)

• High net worth individuals
• Highly skilled technical workers and physicians in the US seeking investment-based immigration opportunities
• Sophisticated private equity investors
• Intermediary partners include domestic attorneys and investment brokers, as well as international agent networks
• US real estate developers

Industry/Entity Type

Finance

Contact Information for Business Card

(Providing placeholder info for personal information, please design for longer character spaces, longer names and addresses etc..)
• Logo for Valdane
• Logo for Thornmere Regional Center
• Full name: Marcus Valdane
• Job title: CEO
• Email address: mvaldane@valdanecompanies.com
• Cell phone number: +1.555.314.2287
• Office number +1.555.628.4410
• Office address: Larkfield Court 5, 4817 Vista Orilla, Corvale, NV.
• Website: www.valdanecompanies.com

Font styles to use
Serif
Sans Serif

Colors
ec1f27
ffffff
000000

Requirements
Must have
• • Logo for Valdane
• • Logo for Thornmere Regional Center
• - Use rounded corners
• (See .ai file included for logos)
Nice to have
• • Simple, elegant design
• • Aesthetically compatible with our website design (www.valdanecompanies.com)
• • Color palette including but not limited to white, black, and red (as per logos)
Should not have
• - Not too much red color
• - Do not stack both logos on top of each other

```html
<!DOCTYPE html>
<html lang="en">
<head>
<meta charset="utf-8">
<title>Valdane Companies Business Card</title>
<link rel="stylesheet" href="https://fonts.googleapis.com/css2?family=Cinzel:wght@500&family=Source+Sans+3:wght@400&display=swap">
<style>
  :root {
    --backdrop: #1b1b1b;
    --card: #efefef;
    --ink: #2b2b2b;
    --ink-soft: #444444;
    --rule: #b9b9b9;
    --brand-red: #b3173a;
    --serif: "Cinzel", serif;
    --sans: "Source Sans 3", sans-serif;
  }
  * { box-sizing: border-box; margin: 0; padding: 0; }
  html, body {
    width: 1200px; height: 900px; overflow: hidden;
    background: var(--backdrop);
  }
  .stage {
    width: 1200px; height: 900px;
    display: flex; flex-direction: column;
    align-items: center; justify-content: center; gap: 50px;
  }
  .card {
    position: relative;
    width: 600px; height: 343px;
    background: var(--card);
    border-radius: 24px;
    overflow: hidden;
  }

  /* Front: regional center */
  .card--front { display: flex; align-items: center; justify-content: center; }
  .center-mark { display: flex; align-items: center; gap: 16px; color: var(--brand-red); }
  .center-mark__square { width: 44px; height: 44px; background: var(--brand-red); }
  .center-mark__name {
    font-family: var(--serif); font-weight: 500;
    display: flex; flex-direction: column; line-height: 1;
  }
  .center-mark__main { font-size: 34px; letter-spacing: 1px; }
  .center-mark__sub { font-size: 11px; letter-spacing: 5px; margin-top: 6px; }

  /* Back: contact side */
  .company-mark {
    position: absolute; top: 52px; left: 250px;
    display: flex; align-items: center; gap: 14px; color: var(--ink);
  }
  .company-mark__square { width: 40px; height: 40px; background: var(--ink-soft); }
  .company-mark__name {
    font-family: var(--serif); font-weight: 500;
    display: flex; flex-direction: column; line-height: 1;
  }
  .company-mark__main { font-size: 32px; letter-spacing: 1px; }
  .company-mark__sub { font-size: 10px; letter-spacing: 6px; margin-top: 6px; }
  .rule-top {
    position: absolute; top: 112px; left: 340px; right: 36px;
    height: 1px; background: var(--rule);
  }
  .contact-list {
    position: absolute; top: 130px; right: 36px;
    list-style: none; text-align: right;
    font-family: var(--sans); font-size: 15px; color: var(--ink); line-height: 19px;
  }
  .contact-list li { display: flex; justify-content: flex-end; align-items: center; gap: 5px; }
  .contact-list svg { width: 13px; height: 13px; fill: var(--ink); }
  .person {
    position: absolute; left: 40px; top: 200px;
  }
  .person__name {
    font-family: var(--serif); font-weight: 500; font-size: 22px;
    color: var(--ink); letter-spacing: 0.5px;
  }
  .person__title {
    font-family: var(--sans); font-size: 15px; color: var(--ink); margin-top: 2px;
  }
  .rule-name {
    position: absolute; top: 214px; left: 275px; width: 150px;
    height: 1px; background: var(--rule);
  }
  .address {
    position: absolute; left: 40px; top: 272px;
    font-family: var(--sans); font-style: normal; font-size: 15px;
    color: var(--ink); line-height: 20px;
  }
</style>
</head>
<body>
<main class="stage">
  <section class="card card--front" aria-label="Card front">
    <div class="center-mark">
      <span class="center-mark__square"></span>
      <span class="center-mark__name">
        <span class="center-mark__main">THORNMERE</span>
        <span class="center-mark__sub">REGIONAL CENTER</span>
      </span>
    </div>
  </section>

  <section class="card card--back" aria-label="Card back">
    <div class="company-mark">
      <span class="company-mark__square"></span>
      <span class="company-mark__name">
        <span class="company-mark__main">VALDANE</span>
        <span class="company-mark__sub">CAPITAL</span>
      </span>
    </div>
    <div class="rule-top"></div>

    <ul class="contact-list">
      <li>+1.555.314.2287
        <svg viewBox="0 0 16 16"><path d="M2 5c0-2 2-3 6-3s6 1 6 3v1h-3V5H5v1H2zM4 7h8l2 6H2z"/></svg></li>
      <li>+1.555.628.4410
        <svg viewBox="0 0 16 16"><path d="M4 1h8v14H4zM5 3v9h6V3z"/></svg></li>
      <li>mvaldane@valdanecompanies.com
        <svg viewBox="0 0 16 16"><path d="M1 3h14v10H1zM2 4.5v.5l6 4 6-4v-.5z"/></svg></li>
      <li>www.valdanecompanies.com
        <svg viewBox="0 0 16 16"><circle cx="8" cy="8" r="7"/></svg></li>
    </ul>

    <div class="person">
      <p class="person__name">MARCUS VALDANE</p>
      <p class="person__title">CEO</p>
    </div>
    <div class="rule-name"></div>

    <address class="address">
      Larkfield Court 5, 4817 Vista<br>
      Orilla, Corvale, NV
    </address>
  </section>
</main>
</body>
</html>
```